Website redesign - vorelmik.com

We are looking to do a full redesign of vorelmik.com. Need a designer to come up overall layout and 3 specific pages and 3 different hero images.
Wireframes for the 3 pages are attached as well as site images. You don't have to follow the wireframes exactly, but instead the wireframe is there to show you the information that needs to be on each page. Feel free to rearrange as needed.
Our target market is self taught engineers. So definitely I want a more casual feel to it. I'm ok with fun bold colors as well. Really like websites that have the infinite scroll look/feel to them.
Looking to find a designer who will produce HTML and potentially even implement the HTML into our site checked in code.
HTML Code should be responsive/mobile first leveraging Bootstrap 4.
Attached files include:
0) Wireframe PDF
https://files.plomwerk.net/d/7Kx2pQmW9zLr4TbN8vYc3HsE5fJ/view?mode=share
1) Vorelmik Images zip 1
https://files.plomwerk.net/d/4Gt8nRvB2wQx6MkZ1pLd9YaC7hU/view?mode=share
2) Vorelmik Images zip 2
https://files.plomwerk.net/d/9Jw3sTcF5yNv1HqX8rKb2ZeM6dP/view?mode=share
Target Market(s)
I sell DIY Waterproof Electronics enclosures. Target audience is self taught DIY engineers
Coding
Coded - Design and coding required
Number of Pages Required
3 page
Colors
Designer to choose colors to be used in the design.
Look and feel

```html
<!DOCTYPE html>
<html lang="en">
<head>
<meta charset="utf-8">
<title>Vorelmik – Waterproof Project Boxes</title>
<link rel="stylesheet" href="https://fonts.googleapis.com/css2?family=Audiowide&family=Montserrat:wght@300;400;500;600;700&display=swap">
<style>
:root{
  --blue:#0a1de6;
  --blue-deep:#0716b8;
  --gold:#f0c214;
  --footer-gold:#f3d53a;
  --ink:#222;
  --muted:#555;
  --soft:#f3f3f3;
  --grey:#ececec;
  --dark:#151515;
  --white:#fff;
}
*{margin:0;padding:0;box-sizing:border-box}
html,body{width:1200px;height:3500px;overflow:hidden}
body{font-family:'Montserrat',sans-serif;color:var(--ink);background:var(--white);position:relative}
.display{font-family:'Audiowide',sans-serif}
.abs{position:absolute}
.btn{position:absolute;display:flex;align-items:center;justify-content:center;font-weight:600;font-size:16px;color:var(--white);background:var(--blue);border-radius:3px;text-decoration:none}
.btn-gold{background:var(--gold);color:var(--ink)}
.underline{position:absolute;width:36px;height:3px;background:var(--gold);left:582px}
.centered{position:absolute;left:0;width:1200px;text-align:center}

/* header */
.site-header{position:absolute;top:0;left:0;width:1200px;height:72px;background:var(--white);border-bottom:1px solid #eee}
.brand{position:absolute;left:160px;top:14px;display:flex;align-items:center;gap:8px;font-weight:700;font-size:38px;color:var(--blue);letter-spacing:-0.5px}
.brand-dot{width:12px;height:12px;border-radius:50%;background:var(--gold)}
.nav a{position:absolute;top:27px;font-size:14px;color:#333;text-decoration:none}
.nav a.active{font-weight:600}
.nav .bar{position:absolute;left:483px;top:68px;width:86px;height:3px;background:var(--blue)}
.nav .login,.nav .signup{top:19px;height:33px;width:72px;display:flex;align-items:center;justify-content:center;color:var(--white);font-weight:600;border-radius:2px}
.nav .login{left:885px;background:var(--gold)}
.nav .signup{left:964px;background:var(--blue)}

/* hero */
.hero{position:absolute;top:72px;left:0;width:1200px;height:491px;background:linear-gradient(180deg,#dcd3b2 0%,#d2c7a2 45%,#c59d6a 62%,#b8874f 100%)}
.hero-photo{position:absolute;left:650px;top:50px;width:550px;height:420px;background:radial-gradient(ellipse at 50% 50%,#5b5148 0%,#7a6c5a 55%,rgba(160,140,110,0) 75%)}
.hero-kicker{position:absolute;left:163px;top:118px;font-weight:300;font-size:41px;color:#222}
.hero-title{position:absolute;left:163px;top:166px;font-size:47px;line-height:55px;color:#111}
.hero-sub{position:absolute;left:163px;top:274px;font-size:25px;font-weight:500;color:#111}
.notch{position:absolute;left:560px;top:531px;width:80px;height:32px}

/* video band */
.video-band{position:absolute;top:563px;left:0;width:1200px;height:409px;background:var(--soft)}
.video-frame{position:absolute;left:160px;top:59px;width:440px;height:294px;background:var(--white);box-shadow:0 2px 10px rgba(0,0,0,.2);padding:7px}
.video-still{width:100%;height:100%;background:linear-gradient(135deg,#6f5a45,#3a3330 55%,#8b8d8f)}
.play{position:absolute;left:201px;top:126px;width:52px;height:32px;background:var(--gold);border-radius:5px}
.band-kicker{position:absolute;left:676px;top:142px;font-size:28px;font-weight:400;color:#333}
.band-title{position:absolute;left:676px;top:174px;font-size:33px;color:#111}

/* kits */
.kits{position:absolute;top:972px;left:0;width:1200px;height:594px;background:linear-gradient(180deg,#fff 0%,#fff 55%,#e2e2e2 100%)}
.kits-kicker{top:58px;font-size:26px;color:#333}
.kits-title{top:92px;font-size:31px;color:#111}
.card3d{position:absolute;background:linear-gradient(180deg,#f2f2f2,#d8d3c8 60%,#bfb5a2)}
.tag{position:absolute;background:var(--gold);font-family:'Audiowide',sans-serif;font-size:14px;color:#111;padding:5px 10px;white-space:nowrap;overflow:hidden}

/* designer band */
.designer{position:absolute;top:1566px;left:0;width:1200px;height:499px;background:var(--blue)}
.designer-photo{position:absolute;left:0;top:0;width:620px;height:499px;background:linear-gradient(135deg,#5a4a36,#b48b5a 40%,#c9a06b 70%,#8d6e4b);clip-path:polygon(0 0,562px 0,620px 499px,0 499px)}
.designer-edge{position:absolute;left:562px;top:0;width:60px;height:499px;background:var(--blue-deep);clip-path:polygon(0 0,38px 0,60px 499px,58px 499px)}
.designer h2{position:absolute;left:663px;font-weight:400}
.designer .k{top:72px;font-size:28px;color:var(--white)}
.designer .t{top:104px;font-family:'Audiowide',sans-serif;font-size:33px;color:var(--gold)}
.designer .lead{position:absolute;left:663px;top:176px;width:440px;font-size:17px;font-weight:600;color:var(--white);line-height:21px}
.features{position:absolute;left:663px;top:232px;list-style:none}
.features li{display:flex;align-items:center;gap:8px;height:24.5px;font-size:14px;color:var(--white)}

/* testimonials */
.reviews{position:absolute;top:2065px;left:0;width:1200px;height:416px;background:var(--white)}
.reviews-title{top:57px;font-size:32px;color:#333}
.reviews-title span{font-family:'Audiowide',sans-serif;color:#111}
.quote{position:absolute;top:168px;width:424px;height:133px;background:var(--white);box-shadow:0 2px 8px rgba(0,0,0,.12);padding:28px 20px 0 36px;font-size:13.5px;line-height:22px;color:#444}
.quote-tail{position:absolute;left:0;bottom:-20px;width:28px;height:20px;background:var(--white);clip-path:polygon(0 0,100% 0,0 100%)}
.quote-mark{position:absolute;left:22px;top:22px}
.reviewer{position:absolute;top:339px;font-size:17px;color:#222}

/* examples */
.examples{position:absolute;top:2481px;left:0;width:1200px;height:825px;background:var(--grey)}
.ex-kicker{top:53px;font-size:26px;color:#333}
.ex-title{top:88px;font-size:31px;color:#111}
.ex-card{position:absolute;width:268px;height:248px;background:var(--white)}
.ex-shot{position:absolute;left:16px;top:16px;width:236px;height:156px;background:radial-gradient(ellipse at 50% 55%,#4a4a4a 0%,#8a8a8a 45%,#f4f4f4 75%)}
.ex-name{position:absolute;left:0;top:186px;width:268px;text-align:center;font-size:14.5px;font-weight:600;line-height:19px;color:#222}

/* footer */
.contact-strip{position:absolute;top:3306px;left:0;width:1200px;height:139px;background:var(--footer-gold)}
.c-icon{position:absolute;width:40px;height:40px;border:3px solid #111;border-radius:50%;display:flex;align-items:center;justify-content:center}
.c-text{position:absolute;font-size:13px;color:#111;line-height:17px}
.c-text b{font-weight:600;font-size:15px}
.c-sep{position:absolute;top:50px;width:1px;height:30px;background:#8a7a20}
.legal{position:absolute;top:3445px;left:0;width:1200px;height:55px;background:var(--dark)}
.legal p{position:absolute;left:163px;top:20px;font-size:12px;color:#ccc}
.social{position:absolute;top:15px;width:26px;height:26px;border-radius:50%;background:#3a3520}
</style>
</head>
<body>

<header class="site-header">
  <div class="brand"><span class="brand-dot"></span>vorelmik</div>
  <nav class="nav">
    <a class="active" style="left:487px">Get Started</a>
    <a style="left:592px">Services</a>
    <a style="left:675px">FAQ's</a>
    <a style="left:741px">Videos</a>
    <a style="left:817px">Contact</a>
    <span class="bar"></span>
    <a class="login">Login</a>
    <a class="signup">Signup</a>
  </nav>
</header>

<section class="hero">
  <div class="hero-photo" role="img" aria-label="Assembled electronics project box with stacked mounting plates, terminal blocks and controller boards on a wooden floor"></div>
  <p class="hero-kicker">waterproof projct boxes</p>
  <h1 class="hero-title display">customised to your<br>exact needs</h1>
  <p class="hero-sub">(at a fraction of the price)</p>
  <a class="btn" style="left:166px;top:326px;width:136px;height:45px">Get Started</a>
  <svg class="notch" viewBox="0 0 80 32" aria-hidden="true">
    <path d="M0 32 C22 32 28 0 40 0 C52 0 58 32 80 32Z" fill="#f3f3f3"/>
    <path d="M40 10 V24 M35 19 L40 24 L45 19" stroke="#d4a90e" stroke-width="1.6" fill="none"/>
  </svg>
</section>

<section class="video-band">
  <div class="video-frame">
    <div class="video-still" role="img" aria-label="Video still of a grey and a black waterproof enclosure mounted outdoors by a brick wall"></div>
    <span class="play"></span>
    <svg class="abs" style="left:220px;top:133px" width="16" height="18" aria-hidden="true"><path d="M0 0 L16 9 L0 18Z" fill="#fff"/></svg>
  </div>
  <h2 class="band-kicker">Customize your project box</h2>
  <h2 class="band-title display">using your designer</h2>
  <a class="btn" style="left:678px;top:240px;width:125px;height:42px">Get Started</a>
</section>

<section class="kits">
  <h2 class="centered kits-kicker" style="font-weight:400">Mounting Kits For all the Popular Water Proof</h2>
  <h2 class="centered kits-title display" style="font-weight:400">project boxes with many sizes to choose from</h2>
  <span class="underline" style="top:144px"></span>

  <div class="card3d" style="left:160px;top:196px;width:92px;height:248px" role="img" aria-label="Enclosure size option"></div>
  <div class="card3d" style="left:252px;top:185px;width:104px;height:268px" role="img" aria-label="Enclosure size option"></div>
  <div class="card3d" style="left:845px;top:185px;width:104px;height:268px" role="img" aria-label="Enclosure size option"></div>
  <div class="card3d" style="left:949px;top:196px;width:92px;height:248px" role="img" aria-label="Enclosure size option"></div>
  <div class="card3d" style="left:355px;top:176px;width:490px;height:293px;background:linear-gradient(180deg,#cfcfcf,#e9e9e9 35%,#d7d0c2 70%,#b9ad97)" role="img" aria-label="Grey hinged waterproof enclosure on a wooden floor"></div>
  <span class="tag" style="left:155px;top:375px;width:97px">Crateon - 3</span>
  <span class="tag" style="left:252px;top:384px;width:104px">Crateon - 32</span>
  <span class="tag" style="left:355px;top:392px">Crateon - 3202</span>
  <span class="tag" style="left:845px;top:384px;width:104px;direction:rtl">Crateon - 3212</span>
  <span class="tag" style="left:949px;top:375px;width:97px;direction:rtl">Crateon - 3210</span>

  <a class="btn" style="left:540px;top:493px;width:125px;height:40px">Get Started</a>
</section>

<section class="designer">
  <div class="designer-photo" role="img" aria-label="Laser-cut mounting plate laid out with controller boards, power supply, standoffs and screws"></div>
  <div class="designer-edge"></div>
  <h2 class="k">Customize your project box</h2>
  <h2 class="t">using your designer</h2>
  <p class="lead">Vorelmik waterproof project boxes were built by makers for makers</p>
  <ul class="features">
    <li><svg width="14" height="14" aria-hidden="true"><rect x="1" y="2" width="11" height="11" fill="none" stroke="#f0c214" stroke-width="1.5"/><path d="M3 7 L6 10 L13 2" stroke="#f0c214" stroke-width="2" fill="none"/></svg>Design to your specifications</li>
    <li><svg width="14" height="14" aria-hidden="true"><rect x="1" y="2" width="11" height="11" fill="none" stroke="#f0c214" stroke-width="1.5"/><path d="M3 7 L6 10 L13 2" stroke="#f0c214" stroke-width="2" fill="none"/></svg>Maker components: Arkline, Pinebit,</li>
    <li><svg width="14" height="14" aria-hidden="true"><rect x="1" y="2" width="11" height="11" fill="none" stroke="#f0c214" stroke-width="1.5"/><path d="M3 7 L6 10 L13 2" stroke="#f0c214" stroke-width="2" fill="none"/></svg>Voltrane Power</li>
    <li><svg width="14" height="14" aria-hidden="true"><rect x="1" y="2" width="11" height="11" fill="none" stroke="#f0c214" stroke-width="1.5"/><path d="M3 7 L6 10 L13 2" stroke="#f0c214" stroke-width="2" fill="none"/></svg>Detailed build instructions, videos, walkthroughs</li>
    <li><svg width="14" height="14" aria-hidden="true"><rect x="1" y="2" width="11" height="11" fill="none" stroke="#f0c214" stroke-width="1.5"/><path d="M3 7 L6 10 L13 2" stroke="#f0c214" stroke-width="2" fill="none"/></svg>DIY made to look professional</li>
  </ul>
  <a class="btn btn-gold" style="left:663px;top:380px;width:125px;height:42px">Get Started</a>
</section>

<section class="reviews">
  <h2 class="centered reviews-title" style="font-weight:400">What Our <span>Customers Have To Say</span></h2>
  <span class="underline" style="top:119px"></span>
  <svg class="abs" style="left:975px;top:131px" width="60" height="14" aria-hidden="true">
    <path d="M2 7 H20 M2 7 L7 2 M2 7 L7 12" stroke="#bbb" stroke-width="1.5" fill="none"/>
    <path d="M32 7 H58 M58 7 L53 2 M58 7 L53 12" stroke="#d4a90e" stroke-width="1.5" fill="none"/>
  </svg>

  <div class="quote" style="left:160px">
    <svg class="quote-mark" width="30" height="24" aria-hidden="true"><path d="M0 24 V10 Q0 0 12 0 V6 Q6 6 6 12 H12 V24Z M17 24 V10 Q17 0 29 0 V6 Q23 6 23 12 H29 V24Z" fill="#f6e7a8"/></svg>
    <span style="padding-left:24px">Great work at a reasonable cost. I can't recommend</span><br>them enough. If you're doing custom boxes for light<br>shows, this is where you go.
    <span class="quote-tail"></span>
  </div>
  <div class="quote" style="left:609px">
    <svg class="quote-mark" width="30" height="24" aria-hidden="true"><path d="M0 24 V10 Q0 0 12 0 V6 Q6 6 6 12 H12 V24Z M17 24 V10 Q17 0 29 0 V6 Q23 6 23 12 H29 V24Z" fill="#f6e7a8"/></svg>
    <span style="padding-left:24px">Fantastic service/product. whether you simply</span><br>generate the design and do all of the fabrication<br>yourself or simply order the kits.
    <span class="quote-tail"></span>
  </div>
  <p class="reviewer" style="left:160px">-Marlo T</p>
  <p class="reviewer" style="left:616px">-Dace K.</p>
</section>

<section class="examples">
  <h2 class="centered ex-kicker" style="font-weight:400">See Real Examples</h2>
  <h2 class="centered ex-title display" style="font-weight:400">From Our Customers</h2>

  <div class="ex-card" style="left:160px;top:166px"><div class="ex-shot" role="img" aria-label="Customer build: controller board on mounting plate"></div><p class="ex-name">Kestral QR8-72 w/ Vantor16 +<br>Expansion board</p></div>
  <div class="ex-card" style="left:465px;top:166px"><div class="ex-shot" role="img" aria-label="Customer build: stacked plates with terminal blocks"></div><p class="ex-name">Kestral QR8-72 w/ Vantor16 +<br>Expansion board</p></div>
  <div class="ex-card" style="left:769px;top:166px"><div class="ex-shot" role="img" aria-label="Customer build: relay modules on black plate"></div><p class="ex-name">Kestral QR8-72 w/ Vantor16 +<br>Expansion board</p></div>
  <div class="ex-card" style="left:160px;top:446px"><div class="ex-shot" role="img" aria-label="Customer build: power supply over controller plate"></div><p class="ex-name">Kestral QR8-72 w/ Vantor16 +<br>Expansion board</p></div>
  <div class="ex-card" style="left:465px;top:446px"><div class="ex-shot" role="img" aria-label="Customer build: power supply on standoffs"></div><p class="ex-name">Kestral QR8-72 w/ Vantor16 +<br>Expansion board</p></div>
  <div class="ex-card" style="left:769px;top:446px"><div class="ex-shot" role="img" aria-label="Customer build: mounted inside an open enclosure"></div><p class="ex-name">Kestral QR8-72 w/ Vantor16 +<br>Expansion board</p></div>

  <a class="btn" style="left:537px;top:725px;width:125px;height:40px">View More</a>
</section>

<footer>
  <div class="contact-strip">
    <div class="c-icon" style="left:161px;top:45px"><svg width="20" height="20" viewBox="0 0 24 24" aria-hidden="true"><path d="M6 2 L10 6 L8 9 Q10 14 15 16 L18 14 L22 18 L19 22 Q8 21 2 6Z" fill="#111"/></svg></div>
    <p class="c-text" style="left:212px;top:46px"><b style="font-size:14px;font-weight:500">Call Us</b><br><span style="font-size:22px;font-weight:500;line-height:28px">123.456.7890</span></p>
    <span class="c-sep" style="left:406px"></span>
    <div class="c-icon" style="left:452px;top:45px"><svg width="18" height="22" viewBox="0 0 18 22" aria-hidden="true"><path d="M9 1 C4 1 1 5 1 9 C1 14 9 21 9 21 C9 21 17 14 17 9 C17 5 14 1 9 1Z" fill="none" stroke="#111" stroke-width="2.2"/><circle cx="9" cy="9" r="3" fill="#111"/></svg></div>
    <p class="c-text" style="left:503px;top:26px"><b style="font-size:14px">Vorelmik Electronics</b><br>200, Building Number, Street Number,<br>State Name, Zip Code</p>
    <span class="c-sep" style="left:788px"></span>
    <div class="c-icon" style="left:843px;top:45px"><svg width="20" height="16" viewBox="0 0 20 16" aria-hidden="true"><rect x="0" y="1" width="20" height="14" rx="2" fill="#111"/><path d="M1 3 L10 9 L19 3" stroke="#f3d53a" stroke-width="1.8" fill="none"/></svg></div>
    <p class="c-text" style="left:894px;top:48px"><b style="font-size:14px">Email Us</b><br>contact@vorelmik.com</p>
  </div>
  <div class="legal">
    <p>Copyright 2020 @ vorelmik designer. All Rights Reserved.</p>
    <span class="social" style="left:970px"></span>
    <span class="social" style="left:1008px"></span>
  </div>
</footer>

</body>
</html>
```